cleaning service

we are a cleaning company,

we have a current flyer but its very dull

I have attached it, can we make it look modern, maybe add pictures and colour

```html
<!DOCTYPE html>
<html lang="en">
<head>
<meta charset="utf-8">
<title>Cleaning Services – Antiviral Sanitisation</title>
<link rel="stylesheet" href="https://fonts.googleapis.com/css2?family=Oswald:wght@400;500;600&family=Roboto+Condensed:wght@400;700&family=Arimo:wght@400&display=swap">
<style>
  :root {
    --cream-top: #ffffff;
    --cream-bottom: #fdf2df;
    --ink: #1c1c1c;
    --brand-red: #962024;
    --sun-yellow: #fdc310;
    --sun-orange: #fbb017;
    --band-light: #fdf0cf;
    --band-mid: #fde6a9;
  }
  * { margin: 0; padding: 0; box-sizing: border-box; }
  html, body { width: 849px; height: 1200px; overflow: hidden; }
  body { font-family: "Arimo", Arial, sans-serif; color: var(--ink); }

  .flyer {
    position: relative;
    width: 849px;
    height: 1200px;
    overflow: hidden;
    background: linear-gradient(180deg, var(--cream-top) 0%, #fefaf1 30%, var(--cream-bottom) 100%);
  }

  .corner-blob { position: absolute; }
  .corner-blob--top { top: 0; right: 0; width: 240px; height: 160px; }
  .corner-blob--bottom { left: 0; bottom: 0; width: 272px; height: 180px; }

  .product-illustration {
    position: absolute;
    left: 670px; top: 20px;
    width: 124px; height: 172px;
    border-radius: 20px;
    background: linear-gradient(160deg, #e9a93a 0%, #3f6fa4 55%, #e6483d 100%);
    opacity: .85;
  }

  .masthead {
    position: absolute;
    left: 84px; top: 56px;
    font-family: "Oswald", "Roboto Condensed", sans-serif;
    font-weight: 600;
    font-size: 19px;
    line-height: 24px;
    letter-spacing: .2px;
    color: var(--ink);
  }
  .masthead .brand { color: var(--brand-red); }

  .faint-bottle {
    position: absolute;
    left: 532px; top: 264px;
    width: 140px; height: 232px;
    border-radius: 30px 30px 22px 22px;
    background: #f6ecdf;
    opacity: .7;
  }

  .service-badge {
    position: absolute;
    left: 84px; top: 334px;
    width: 103px; height: 103px;
    border: 1.4px solid var(--brand-red);
    border-radius: 50%;
    display: flex; align-items: center; justify-content: center;
  }
  .service-badge .badge-art {
    width: 34px; height: 68px;
    border-radius: 8px;
    background: var(--brand-red);
  }

  .service-title {
    position: absolute;
    left: 84px; top: 458px;
    font-family: "Roboto Condensed", "Oswald", sans-serif;
    font-weight: 700;
    font-size: 26px;
    color: var(--brand-red);
  }

  .service-copy {
    position: absolute;
    top: 512px;
    width: 335px;
    font-size: 16.4px;
    line-height: 22.8px;
  }
  .service-copy--left { left: 84px; }
  .service-copy--right { left: 442px; }
  .service-copy .lead { margin-bottom: 4px; }
  .highlight {
    font-family: "Roboto Condensed", sans-serif;
    font-weight: 700;
    color: var(--brand-red);
    font-size: 17px;
  }

  .price-band {
    position: absolute;
    left: 172px; top: 835px;
    width: 543px; height: 76px;
    border-radius: 30px;
    background: linear-gradient(180deg, rgba(253,240,207,0) 0%, var(--band-light) 25%, var(--band-mid) 100%);
    display: flex; align-items: center; justify-content: center;
    font-family: "Roboto Condensed", sans-serif;
    font-weight: 700;
    font-size: 22px;
    color: var(--ink);
    gap: 6px;
  }
  .price-band .price { color: var(--brand-red); font-size: 30px; margin-left: 4px; }
  .price-band .unit { font-weight: 400; }
  .price-band .unit b { font-weight: 700; }

  .contact-strip {
    position: absolute;
    left: 383px; top: 1081px;
    width: 466px; height: 61px;
    border-radius: 30px 0 0 30px;
    border-top: 1.5px solid var(--sun-orange);
    background: linear-gradient(180deg, #fefaf0 0%, #fde9b9 70%, var(--sun-orange) 100%);
    padding: 10px 0 0 32px;
    font-family: "Roboto Condensed", sans-serif;
    font-weight: 700;
  }
  .contact-strip .note { font-size: 11px; color: var(--ink); line-height: 13px; }
  .contact-strip .call { font-size: 20px; color: var(--brand-red); line-height: 26px; }
</style>
</head>
<body>
<main class="flyer">
  <svg class="corner-blob corner-blob--top" viewBox="0 0 240 160" aria-hidden="true">
    <defs>
      <linearGradient id="sunTop" x1="0" y1="0" x2="1" y2="0">
        <stop offset="0" stop-color="#fbb017"/>
        <stop offset="1" stop-color="#fdd10e"/>
      </linearGradient>
    </defs>
    <path d="M62 0 C70 30 100 42 140 48 C190 56 210 100 226 150 C232 160 240 158 240 150 L240 0 Z" fill="url(#sunTop)"/>
  </svg>

  <div class="product-illustration" role="img" aria-label="Illustration of cleaning products: spray bottle, detergent bottles and a sponge"></div>

  <header class="masthead">
    <div>CLEANING SERVICES</div>
    <div>by <span class="brand">MAPLE LANE</span></div>
  </header>

  <div class="faint-bottle" role="img" aria-label="Faint decorative spray bottle"></div>

  <div class="service-badge">
    <div class="badge-art" role="img" aria-label="Spray bottle icon"></div>
  </div>

  <h1 class="service-title">Antiviral Sanitisation Service</h1>

  <p class="service-copy service-copy--left">
    The cleaning specialists will use <span class="highlight">professional equipment</span> and will wipe all washable surfaces down in order to eradicate and disinfect from all the harmful germs. Our broad spectrum and <span class="highlight">certified disinfectant</span> is perfect for disease control or precautionary measure in any property or business, in order to ensure and maintain hygienic conditions. Our antiviral sanitisation service can be requested separately or combined with any of our other services.
  </p>

  <div class="service-copy service-copy--right">
    <p class="lead">BS EN 1276 is the European standard for</p>
    <p>the bactericidal activity of chemical disinfectants as proof of effective infection control against harmful micro-organisms such as MRSA, Salmonella, E.Coli, Flu Virus (H1N1)&nbsp; HIV(AIDS), T.B, SARS, Hepatitis, Influenza A. In order to pass this standard, products have been tested by an independent laboratory and must prove a <span class="highlight">bacterium kill rate of 99.999% within 5 minutes.</span></p>
  </div>

  <div class="price-band">
    <span>Including our cleaning materials</span>
    <span class="price">£16</span>
    <span class="unit">(per hour)</span>
  </div>

  <svg class="corner-blob corner-blob--bottom" viewBox="0 0 272 180" aria-hidden="true">
    <defs>
      <linearGradient id="sunBottom" x1="0" y1="0" x2="1" y2="0">
        <stop offset="0" stop-color="#fdd10e"/>
        <stop offset="1" stop-color="#fbb017"/>
      </linearGradient>
    </defs>
    <path d="M0 0 C16 10 20 50 40 70 C70 100 110 90 140 100 C190 118 220 140 272 180 L0 180 Z" fill="url(#sunBottom)"/>
  </svg>

  <footer class="contact-strip">
    <div class="note">Please turnover for our services and prices</div>
    <div class="call">Please call us on 07700900461 to beat any price</div>
  </footer>
</main>
</body>
</html>
```